QP Fiduciary Website Redesign Contest

We want to refresh our website to be more insitutional, professional for an international audience. We have designed a new logo for this purpose and that has been attached. A full brand brief and positioning statement has also been attached. Please read through all the documents carefully before designing. The old website is found here: https://qp-fiduciary.example/

Target Market(s)

Actuaries and associated businesses internationally

Industry/Entity Type

professional services - actuaries

Number of Pages Required

3 page

Font styles to use
Sans Serif

Colors
0054AA
0677BA
7BADD7
CADEEF
E8F1F8
0094D4
00A9DD
6FCCEA
C7EBF8
E9F6FB
F0912C
F2A743
F7CA91
FBE8D2
FDF5EE
EE7325
F08F49
F5BC92
FAE3D3
FDF4ED
EB3D1F
EC4F4E
F09395
F8D3D4
FCEDEE

Requirements
Must have
• blues and greens to match the logo color, complimentary colors, navigation
Nice to have
• old site: https://qp-fiduciary.example/

```html
<!DOCTYPE html>
<html lang="en">
<head>
<meta charset="utf-8">
<title>QP Fiduciary — Actuarial Software</title>
<link href="https://fonts.googleapis.com/css2?family=Roboto:wght@400;500;700;900&family=Fira+Sans:wght@400;500;600&display=swap" rel="stylesheet">
<style>
:root{
  --navy:#133a96;
  --navy-deep:#0f2f86;
  --green:#1f8b6c;
  --teal:#52c8b0;
  --steel:#5f8ccb;
  --ink:#1b1b1b;
  --text:#333;
  --muted:#dcdcdc;
  --soft:#f1f2f4;
  --white:#fff;
}
*{margin:0;padding:0;box-sizing:border-box}
html,body{width:1200px;height:4376px;overflow:hidden}
body{position:relative;background:var(--white);font-family:"Fira Sans",sans-serif;color:var(--text)}
.abs{position:absolute}
.center{left:0;width:1200px;text-align:center}
h1,h2{font-family:"Roboto",sans-serif;font-weight:900;color:var(--ink);letter-spacing:-0.5px}
.rule{position:absolute;left:546px;width:109px;height:4px;background:var(--green)}
.btn{position:absolute;display:flex;align-items:center;justify-content:center;gap:10px;border-radius:26px;color:#fff;font-family:"Roboto",sans-serif;font-weight:700;font-size:14px;text-decoration:none}
.btn svg{width:20px;height:14px}
.btn-navy{background:var(--navy)}
.btn-green{background:var(--green);border:2px solid var(--navy-deep)}

/* header */
.logo{font-family:"Roboto",sans-serif;font-weight:500;font-size:24px;letter-spacing:1px;color:var(--navy);display:flex;align-items:center;gap:10px}
.logo .dot{width:12px;height:12px;border-radius:50%;background:var(--green)}
.nav{left:396px;top:24px;display:flex;font-family:"Roboto",sans-serif;font-size:14px;color:#333}
.nav a{color:inherit;text-decoration:none;padding:0 16px;border-left:1px solid #bbb;line-height:20px}
.nav a:first-child{border-left:none;padding-left:0;color:var(--green)}
.login{left:940px;top:14px;width:151px;height:44px;border:2px solid var(--navy);border-radius:24px;display:flex;align-items:center;justify-content:center;gap:6px;font-family:"Roboto",sans-serif;font-weight:700;font-size:14px;color:var(--navy)}

/* hero */
.hero-title{top:150px;font-size:50px;line-height:56px}
.hero-title .accent{color:var(--green)}
.hero-sub{top:333px;font-size:15px;line-height:22px;color:#222}
.network{left:0;top:360px;width:1200px;height:700px;background:radial-gradient(ellipse at 50% 50%,#eef0f2 0%,#f8f9fa 50%,#fff 80%)}

/* overview */
.overview-text{top:1160px;font-size:18px;line-height:28px;color:#222}
.steps{left:0;top:1328px;width:1200px;height:200px}

/* solutions */
.solutions{left:0;top:1644px;width:1200px;height:714px;background:linear-gradient(135deg,#1a3c9c 0%,#0f2f88 60%,#123590 100%)}
.solutions h2{color:#fff}
.card{position:absolute;background:#fff;border:3px solid #c9cfdc;border-radius:10px;text-align:center;padding:0 22px}
.card h3{font-family:"Roboto",sans-serif;font-weight:700;font-size:22px;line-height:31px;color:#111}
.card .bar{width:64px;height:3px;background:#ccc;margin:16px auto}
.card p{font-size:15px;line-height:24px;color:#222}
.card svg{display:block;margin:0 auto 14px}

/* characteristics */
.trait{position:absolute;width:434px;height:116px;background:#fff;border-radius:8px;box-shadow:0 4px 18px rgba(0,0,0,.09);display:flex;align-items:center;gap:18px;padding:0 28px;font-size:18px;line-height:28px;color:#222}
.trait.right{justify-content:flex-end;text-align:right}
.num{flex:none;width:52px;height:52px;border-radius:50%;background:var(--green);color:#fff;font-family:"Roboto",sans-serif;font-weight:700;font-size:16px;display:flex;align-items:center;justify-content:center}

/* articles */
.articles{left:0;top:2946px;width:1200px;height:629px;background:linear-gradient(120deg,#eceef1 0%,#f7f8f9 45%,#e9ebee 100%)}
.article{position:absolute;left:228px;width:743px;height:80px;border-bottom:2px solid #c9c9c9;display:flex;align-items:center;justify-content:space-between;font-size:22px;color:#222}
.arrow-dot{width:32px;height:32px;border-radius:50%;background:#dfe4ef;display:flex;align-items:center;justify-content:center}
.arrow-dot.active{background:var(--navy)}

/* footer */
.footer{left:0;top:3978px;width:1200px;height:398px;background:linear-gradient(135deg,#1a3d9e,#103089)}
.footer .logo{color:#fff;font-size:30px}
.foot-head{font-family:"Roboto",sans-serif;font-weight:700;font-size:24px;color:#fff}
.foot-links a{display:block;color:#fff;text-decoration:none;font-size:18px;line-height:32px}
.contact-item{display:flex;gap:12px;color:#fff;font-size:14px;line-height:17px;margin-bottom:20px}
.contact-item b{font-family:"Roboto",sans-serif;font-weight:700;display:block}
.copy{top:4314px;color:#fff;font-size:17px}
</style>
</head>
<body>

<!-- header -->
<div class="abs logo" style="left:110px;top:20px"><span class="dot"></span>QP FIDUCIARY</div>
<nav class="abs nav">
  <a href="#">Home</a><a href="#">Platform</a><a href="#">Solutions</a><a href="#">Insights</a><a href="#">Company</a><a href="#">Contact</a>
</nav>
<div class="abs login">
  <svg width="12" height="13" viewBox="0 0 12 13"><circle cx="6" cy="3.5" r="3" fill="#1f8b6c"/><path d="M0 13c0-4 2.5-6 6-6s6 2 6 6z" fill="#1f8b6c"/></svg>
  Client Login
</div>

<!-- hero -->
<div class="abs network" role="img" aria-label="Soft grey network of connected nodes and lines spanning the page"></div>
<h1 class="abs center hero-title">ACTUARIAL SOFTWARE FOR<br><span class="accent">STRUCTURED, AUDITABLE</span><br>FINANCIAL ANALYSIS.</h1>
<p class="abs center hero-sub">QP Fiduciary develops software that translates established<br>actuarial methodologies into disciplined, decision-ready tools.</p>
<a class="btn btn-navy" href="#" style="left:449px;top:391px;width:302px;height:46px">Request a technical walkthrough
  <svg viewBox="0 0 20 14"><path d="M1 7h17M12 1l6 6-6 6" stroke="#fff" stroke-width="2" fill="none"/></svg></a>

<!-- overview -->
<h2 class="abs center" style="top:1050px;font-size:48px">PLATFORM OVERVIEW</h2>
<div class="rule" style="top:1134px"></div>
<p class="abs center overview-text">QP Fiduciary develops modular actuarial software designed to support reserving,<br>valuation, pricing, and risk analysis workflows across diverse regulatory environments.</p>
<a class="btn btn-navy" href="#" style="left:501px;top:1239px;width:199px;height:48px">Explore Platform
  <svg viewBox="0 0 20 14"><path d="M1 7h17M12 1l6 6-6 6" stroke="#fff" stroke-width="2" fill="none"/></svg></a>

<svg class="abs steps" viewBox="0 0 1200 200" role="img" aria-label="Four connected platform modules: collaboration, valuation, pricing and growth analytics">
  <line x1="243" y1="100" x2="955" y2="100" stroke="#d7e4ef" stroke-width="10"/>
  <g>
    <circle cx="243" cy="100" r="99" fill="#5f8ccb"/><circle cx="249" cy="100" r="63" fill="#fff" filter="drop-shadow(0 4px 6px rgba(0,0,0,.2))"/>
    <circle cx="481" cy="100" r="99" fill="#52c8b0"/><circle cx="487" cy="100" r="63" fill="#fff"/>
    <circle cx="719" cy="100" r="99" fill="#5f8ccb"/><circle cx="725" cy="100" r="63" fill="#fff"/>
    <circle cx="955" cy="100" r="99" fill="#52c8b0"/><circle cx="961" cy="100" r="63" fill="#fff"/>
  </g>
  <g stroke="#133a96" stroke-width="3" fill="none">
    <rect x="467" y="82" width="40" height="30" rx="3"/><path d="M478 104v-8M487 104v-14M496 104v-10"/>
    <circle cx="725" cy="100" r="16"/><path d="M725 92v16M720 96h8M720 104h8"/>
    <path d="M938 118v-12M950 118v-20M962 118v-16M974 118v-28M936 100l14-10 12 4 14-14"/>
    <path d="M230 110l14-14 10 6 12-12M232 96l10 10M250 112l14-12"/>
  </g>
</svg>

<!-- solutions -->
<section class="abs solutions">
  <h2 class="abs center" style="top:89px;font-size:48px;color:#fff">CORE SOLUTIONS</h2>
  <div class="rule" style="top:171px"></div>
</section>
<div class="card" style="left:143px;top:1858px;width:284px;height:342px;padding-top:42px">
  <svg width="60" height="60" viewBox="0 0 60 60" fill="none" stroke="#133a96" stroke-width="2.5"><rect x="8" y="6" width="34" height="46" rx="3"/><circle cx="25" cy="22" r="9"/><path d="M15 40h20M15 46h14M40 44l14-14 4 4-14 14z" stroke="#1f8b6c"/></svg>
  <h3>Reserving &amp;<br>Valuation</h3><div class="bar"></div>
  <p>Software supporting structured reserving workflows and financial reporting across jurisdictions.</p>
</div>
<div class="card" style="left:459px;top:1884px;width:282px;height:355px;padding-top:38px">
  <svg width="60" height="60" viewBox="0 0 60 60" fill="none" stroke="#133a96" stroke-width="2.5"><ellipse cx="20" cy="40" rx="14" ry="5"/><path d="M6 40v8c0 3 6 5 14 5s14-2 14-5v-8"/><circle cx="40" cy="38" r="12"/><path d="M40 20V4M34 10l6-6 6 6" stroke="#1f8b6c"/></svg>
  <h3>Pricing</h3><div class="bar"></div>
  <p>Models supporting insurance and reinsurance pricing based on actuarial methodologies.</p>
</div>
<a class="btn btn-green" href="#" style="left:517px;top:2215px;width:166px;height:43px">Learn More
  <svg viewBox="0 0 20 14"><path d="M1 7h17M12 1l6 6-6 6" stroke="#fff" stroke-width="2" fill="none"/></svg></a>
<div class="card" style="left:773px;top:1858px;width:284px;height:342px;padding-top:42px">
  <svg width="60" height="60" viewBox="0 0 60 60" fill="none" stroke="#133a96" stroke-width="2.5"><circle cx="30" cy="20" r="12"/><circle cx="30" cy="20" r="5" stroke="#1f8b6c"/><circle cx="14" cy="44" r="5"/><circle cx="30" cy="44" r="5"/><circle cx="46" cy="44" r="5"/><path d="M6 58c0-5 3-8 8-8s8 3 8 8M22 58c0-5 3-8 8-8s8 3 8 8M38 58c0-5 3-8 8-8s8 3 8 8"/></svg>
  <h3>Enterprise Risk<br>Management</h3><div class="bar"></div>
  <p>Software supporting reinsurance optimization and capital modeling.</p>
</div>

<!-- characteristics -->
<h2 class="abs center" style="top:2438px;font-size:48px">PLATFORM CHARACTERISTICS</h2>
<div class="rule" style="top:2524px"></div>
<div class="trait" style="left:144px;top:2562px"><span class="num">01</span>Structured workflows suitable for<br>multi-jurisdictional review</div>
<div class="trait" style="left:144px;top:2717px"><span class="num">02</span>Transparent assumptions and<br>methodological clarity</div>
<div class="trait right" style="left:620px;top:2562px">Comparative scenario analysis<span class="num">03</span></div>
<div class="trait right" style="left:620px;top:2717px">Supports professional judgment<br>rather than replacing it<span class="num">04</span></div>
<svg class="abs" style="left:518px;top:2612px" width="164" height="164" viewBox="0 0 164 164">
  <circle cx="82" cy="82" r="80" fill="#fff" filter="drop-shadow(0 3px 6px rgba(0,0,0,.15))"/>
  <circle cx="82" cy="82" r="61" fill="#133a96"/>
  <g fill="none" stroke="#fff" stroke-width="3"><circle cx="82" cy="70" r="13"/><circle cx="82" cy="70" r="5"/><circle cx="66" cy="92" r="5"/><circle cx="82" cy="92" r="5"/><circle cx="98" cy="92" r="5"/><path d="M58 108c0-5 3-8 8-8s8 3 8 8M74 108c0-5 3-8 8-8s8 3 8 8M90 108c0-5 3-8 8-8s8 3 8 8"/></g>
</svg>

<!-- articles -->
<section class="abs articles">
  <h2 class="abs center" style="top:85px;font-size:48px">RECENT ARTICLES</h2>
  <div class="rule" style="top:170px"></div>
</section>
<div class="article" style="top:3136px">Methodological perspectives in actuarial reserving
  <span class="arrow-dot active"><svg width="12" height="12" viewBox="0 0 12 12"><path d="M2 10L10 2M4 2h6v6" stroke="#fff" stroke-width="1.8" fill="none"/></svg></span></div>
<div class="article" style="top:3216px">Governance considerations in multi-jurisdictional analysis
  <span class="arrow-dot"><svg width="12" height="12" viewBox="0 0 12 12"><path d="M2 10L10 2M4 2h6v6" stroke="#133a96" stroke-width="1.8" fill="none"/></svg></span></div>
<div class="article" style="top:3296px">Observations on actuarial practice in emerging markets
  <span class="arrow-dot"><svg width="12" height="12" viewBox="0 0 12 12"><path d="M2 10L10 2M4 2h6v6" stroke="#133a96" stroke-width="1.8" fill="none"/></svg></span></div>
<a class="btn btn-green" href="#" style="left:517px;top:3409px;width:166px;height:44px">Read Insights
  <svg viewBox="0 0 20 14"><path d="M1 7h17M12 1l6 6-6 6" stroke="#fff" stroke-width="2" fill="none"/></svg></a>

<!-- CTA -->
<div class="abs" style="left:0;top:3730px;width:1200px;height:248px;background:linear-gradient(180deg,#fff 0%,#f1f2f4 100%)" role="img" aria-label="Faint network of connected nodes behind the call to action"></div>
<h2 class="abs center" style="top:3655px;font-size:48px;line-height:57px">INTERESTED IN EXPLORING<br>THE PLATFORM?</h2>
<div class="rule" style="top:3797px"></div>
<a class="btn btn-green" href="#" style="left:445px;top:3818px;width:310px;height:46px">Request a Technical Walkthrough
  <svg viewBox="0 0 20 14"><path d="M1 7h17M12 1l6 6-6 6" stroke="#fff" stroke-width="2" fill="none"/></svg></a>

<!-- footer -->
<footer class="abs footer">
  <div class="abs logo" style="left:144px;top:83px"><span class="dot" style="background:#fff"></span>QP FIDUCIARY</div>
  <span class="abs" style="left:143px;top:158px;width:48px;height:48px;border-radius:50%;background:#fff" role="img" aria-label="Professional network profile link"></span>
  <div class="abs foot-head" style="left:554px;top:88px">Company</div>
  <div class="abs foot-links" style="left:554px;top:135px">
    <a href="#">Platform</a><a href="#">Solutions</a><a href="#">Insights</a><a href="#">Contact</a>
  </div>
  <div class="abs foot-head" style="left:819px;top:88px">Contact</div>
  <div class="abs" style="left:822px;top:136px">
    <div class="contact-item"><svg width="10" height="12" viewBox="0 0 10 12"><path d="M5 12S0 7 0 4.5a5 5 0 0110 0C10 7 5 12 5 12z" fill="#fff"/><circle cx="5" cy="4.5" r="1.8" fill="#133a96"/></svg><span><b>Address :</b>12, Lorem ipsum dolor</span></div>
    <div class="contact-item"><svg width="11" height="11" viewBox="0 0 11 11"><path d="M2 0l2 2.5-1 1.5c.6 1.5 2 2.9 3.5 3.5l1.5-1 2.5 2-1 2C4 10.5.5 7 0 1z" fill="#fff"/></svg><span><b>Phone :</b>+1 888 888 8888</span></div>
    <div class="contact-item"><svg width="12" height="10" viewBox="0 0 12 10"><rect width="12" height="10" rx="1" fill="#fff"/><path d="M0 1l6 4 6-4" stroke="#133a96" fill="none"/></svg><span><b>Email Address :</b>info@companyname.com</span></div>
  </div>
</footer>
<p class="abs center copy">© Copyrights 2026 | All Rights Reserved</p>

</body>
</html>
```